Brimwell Sorrel Organic

Please find attached screenshots of a same product as what I'm selling, looking for similar packaging but yet a whole new different design with my own logo tidemarrows which is also attached. It will be on white bags with the clear on the bottom center. As far as colors maby green yellow and black or if you have a better idea. Also it needs to be something that looks up to date modern I like when it has that two-tone gloss to it where it goes from darker to lighter.

```html
<!DOCTYPE html>
<html lang="en">
<head>
<meta charset="utf-8">
<title>Brimwell Sorrel Organic – Pouch Label</title>
<link href="https://fonts.googleapis.com/css2?family=Lilita+One&family=Poppins:wght@400;500;600&display=block" rel="stylesheet">
<style>
  :root {
    --night: #001200;
    --forest: #224936;
    --base: #010e03;
    --leaf: #62bb46;
    --window: #bebfc1;
    --white: #ffffff;
  }
  * { margin: 0; padding: 0; box-sizing: border-box; }
  html, body { width: 857px; height: 1200px; overflow: hidden; background: var(--white); }
  .label {
    position: relative;
    width: 857px;
    height: 1200px;
    overflow: hidden;
    background: var(--night);
    font-family: "Poppins", sans-serif;
    color: var(--white);
  }
  .header {
    position: absolute;
    inset: 0 0 auto 0;
    height: 592px;
    background: var(--night);
  }
  .brand {
    position: absolute;
    top: 216px;
    left: 0;
    width: 100%;
    text-align: center;
  }
  .brand-dot {
    display: block;
    width: 116px;
    height: 116px;
    margin: 0 auto;
    border-radius: 50%;
    background: var(--white);
  }
  .brand-name {
    display: block;
    margin-top: 40px;
    font-family: "Poppins", sans-serif;
    font-weight: 600;
    font-size: 40px;
    letter-spacing: 6px;
    line-height: 1;
    color: var(--white);
  }
  .product-title {
    position: absolute;
    top: 458px;
    left: 0;
    width: 100%;
    text-align: center;
    font-family: "Lilita One", "Arial Black", sans-serif;
    font-weight: 400;
    font-size: 80px;
    line-height: 1;
    letter-spacing: 1px;
    color: var(--white);
  }
  .product-tagline {
    position: absolute;
    top: 552px;
    left: 0;
    width: 100%;
    text-align: center;
    padding-left: 8px;
    font-weight: 500;
    font-size: 22px;
    letter-spacing: 4px;
    line-height: 1;
  }
  .showcase {
    position: absolute;
    top: 592px;
    left: 0;
    width: 857px;
    height: 527px;
    background: var(--forest);
  }
  .showcase svg { display: block; }
  .seal-ring-text {
    font-family: "Poppins", sans-serif;
    font-weight: 400;
    font-size: 38px;
    letter-spacing: 2px;
    fill: var(--white);
  }
  .seal-center-text {
    font-family: "Poppins", sans-serif;
    font-weight: 500;
    font-size: 40px;
    letter-spacing: 3px;
    fill: var(--white);
  }
  .footer {
    position: absolute;
    top: 1119px;
    left: 0;
    width: 857px;
    height: 81px;
    background: var(--base);
    display: flex;
    align-items: center;
    justify-content: center;
  }
  .net-weight {
    font-weight: 500;
    font-size: 25px;
    letter-spacing: 4px;
    padding-left: 16px;
  }
</style>
</head>
<body>
  <main class="label">
    <section class="header" role="img" aria-label="Dark green background with faint line drawings of sorrel leaves and flowers"></section>

    <div class="brand">
      <span class="brand-dot"></span>
      <span class="brand-name">TIDEMARROWS</span>
    </div>

    <h1 class="product-title">BRIMWELL SORREL</h1>
    <p class="product-tagline">100% HERBAL</p>

    <section class="showcase">
      <svg width="857" height="527" viewBox="0 1122 1624 998" aria-label="Clear window showing the product with a quality seal">
        <defs>
          <path id="seal-arc-top" d="M 362 1815 A 135 135 0 0 1 632 1815"/>
          <path id="seal-arc-bottom" d="M 335 1815 A 162 162 0 0 0 659 1815"/>
        </defs>
        <path class="window"
          d="M900 1177 C1010 1177 1090 1222 1150 1290 L1240 1395 C1305 1470 1330 1570 1293 1676 L1253 1791
             C1215 1915 1115 1998 998 2018 L878 2038 C772 2056 686 2025 606 1968
             L420 1660 C420 1585 432 1515 452 1455 L477 1383 C520 1262 606 1222 722 1201 Z"
          fill="var(--window)" stroke="var(--leaf)" stroke-width="28" stroke-linejoin="round"/>
        <g class="quality-seal">
          <circle cx="497" cy="1815" r="194" fill="var(--leaf)"/>
          <circle cx="497" cy="1815" r="178" fill="var(--forest)"/>
          <circle cx="497" cy="1815" r="116" fill="var(--leaf)"/>
          <text class="seal-ring-text" text-anchor="middle">
            <textPath href="#seal-arc-top" startOffset="50%">PREMIUM</textPath>
          </text>
          <text class="seal-ring-text" text-anchor="middle">
            <textPath href="#seal-arc-bottom" startOffset="50%">QUALITY</textPath>
          </text>
          <text class="seal-center-text" x="499" y="1832" text-anchor="middle">ORGANIC</text>
          <g fill="var(--white)" opacity="0.9">
            <circle cx="386" cy="1712" r="7"/>
            <circle cx="607" cy="1712" r="7"/>
            <circle cx="386" cy="1922" r="7"/>
            <circle cx="607" cy="1922" r="7"/>
          </g>
        </g>
      </svg>
    </section>

    <footer class="footer">
      <p class="net-weight">NET WEIGHT 2.47 OZ. (70g)</p>
    </footer>
  </main>
</body>
</html>
```